Business Card Design

We provide services doing multiple jobs in the construction industry.Please note: The company name needs to be ROCK SOLID BUILDING SERVICESAttached logo was an example of what we wanted. Can you change up the colors?

Industry/Entity Type

Construction

Contact Information for Business Card

ROCK SOLID BUILDING SERVICES5401 HUDSON BEND RDAUSTIN, TX 78734(512)243-6854ROCKSOLIDBUILDINGSERVICES@GMAIL.COM

```html
<!DOCTYPE html>
<html lang="en">
<head>
<meta charset="utf-8">
<title>Pearlwood Framing Works – Business Card</title>
<link rel="stylesheet" href="https://fonts.googleapis.com/css2?family=Oswald:wght@500;700&family=Arimo:wght@400&display=swap">
<style>
  :root {
    --navy: #2b2470;
    --navy-deep: #221c5e;
    --teal: #5f8797;
    --paper: #ffffff;
    --backdrop: #eeeeef;
    --ridge: #b9b7cf;
  }
  html, body {
    margin: 0;
    padding: 0;
    width: 1200px;
    height: 864px;
    overflow: hidden;
    background: var(--backdrop);
  }
  .canvas {
    position: relative;
    width: 1200px;
    height: 864px;
  }
  .card {
    position: absolute;
    left: 75px;
    top: 132px;
    width: 1050px;
    height: 600px;
    background: var(--paper);
    overflow: hidden;
    box-shadow: 0 18px 40px rgba(0,0,0,0.14);
  }
  .card__swoosh {
    position: absolute;
    inset: 0;
    width: 100%;
    height: 100%;
  }
  .card__header {
    position: absolute;
    right: 50px;
    top: 52px;
    text-align: right;
    color: var(--paper);
  }
  .card__header-name {
    font-family: "Oswald", sans-serif;
    font-weight: 700;
    font-size: 66px;
    line-height: 1;
    letter-spacing: 0.5px;
  }
  .card__header-sub {
    font-family: "Arimo", sans-serif;
    font-size: 21px;
    margin-top: 6px;
    margin-right: 30px;
  }
  .card__ridge {
    position: absolute;
    left: 770px;
    top: 185px;
    width: 230px;
    height: 80px;
    border-radius: 40px 40px 6px 6px;
    background: linear-gradient(180deg, rgba(185,183,207,0.55), rgba(185,183,207,0.15));
  }
  .card__brand {
    position: absolute;
    left: 120px;
    top: 150px;
    width: 330px;
    display: flex;
    align-items: center;
    gap: 14px;
    color: var(--navy);
  }
  .card__brand-mark {
    width: 26px;
    height: 26px;
    flex: none;
    background: var(--navy);
  }
  .card__brand-name {
    font-family: "Oswald", sans-serif;
    font-weight: 700;
    font-size: 44px;
    line-height: 1.05;
  }
  .card__contact {
    position: absolute;
    left: 90px;
    top: 388px;
    width: 660px;
    text-align: center;
    font-family: "Arimo", sans-serif;
    font-size: 24px;
    line-height: 1.55;
    color: var(--navy-deep);
    text-transform: uppercase;
  }
  .card__contact p { margin: 0; }
</style>
</head>
<body>
<main class="canvas">
  <article class="card">
    <svg class="card__swoosh" viewBox="0 0 1050 600" preserveAspectRatio="none" aria-hidden="true">
      <path d="M430,0 Q770,120 860,600 L1050,600 L1050,0 Z" fill="var(--teal)"/>
      <path d="M505,0 Q820,125 912,600 L1050,600 L1050,0 Z" fill="var(--navy)"/>
    </svg>

    <header class="card__header">
      <div class="card__header-name">PEARLWOOD</div>
      <div class="card__header-sub">FRAMING WORKS</div>
    </header>

    <div class="card__ridge" role="img" aria-label="Outline of mountain peaks"></div>

    <div class="card__brand">
      <span class="card__brand-mark"></span>
      <span class="card__brand-name">PEARLWOOD FRAMING WORKS</span>
    </div>

    <address class="card__contact" style="font-style:normal">
      <p class="card__phone">(512)555-0193</p>
      <p class="card__address">7732 FERNGLEN PASS LN AUSTIN, TX 78734</p>
      <p class="card__email">PEARLWOODFRAMINGWORKS@MAILNEST.EXAMPLE</p>
    </address>
  </article>
</main>
</body>
</html>
```